Provide bookkeeping and accounting services to small and growing businesses

We need website and logo design using the name Dornaby as the logo.
The target audience are small companies and startups who need:
1) Simple bookkeeping services
2) Accounting advice that only someone with many years of senior financial experience as a CPA can provide.

The services are provided by two individuals. each of whom specialize in one of the areas.

We want the website to be clean without a lot of visual distraction but don't know how to make a boring subject interesting. We believe our potential clients, small business owners, need to find what they want quickly and easily without a lot of verbiage or distractions.

We've attached a draft of the homepage and have completed the text on most of the other pages.

Target Market(s)

small and early stage growth companies in San Diego North County

Industry/Entity Type

Accounting

Number of Pages Required

1 page

Font styles to use
Sans Serif

Colors
86cfc6
33b8a4
85cae6

Requirements
Must have
• We need a design for the website homepage that includes the name Dornaby as the logo. Must include a design for the name.
• Must have color in teal or greenish blue.
Nice to have
• White background, clean, clear, uncluttered.
• We would like to use the design in a Theme on a WordPress website. Themes Paper Lantern and Quiet Harbour are appealing to us.
Should not have
• Moving pictures

```html
<!DOCTYPE html>
<html lang="en">
<head>
<meta charset="utf-8">
<title>Dornaby – Bookkeeping &amp; Accounting</title>
<link href="https://fonts.googleapis.com/css2?family=Montserrat:wght@400;500;700&display=swap" rel="stylesheet">
<style>
  :root {
    --teal: #33b8a4;
    --teal-soft: #5cc4b3;
    --ink: #111111;
    --paper: #ffffff;
    --photo-a: #b9d3e6;
    --photo-b: #e8e2cf;
  }
  * { margin: 0; padding: 0; box-sizing: border-box; }
  html, body {
    width: 1200px; height: 1200px; overflow: hidden;
    background: var(--paper);
    font-family: "Montserrat", Arial, sans-serif;
  }
  .site {
    position: absolute; left: 0; top: 274px;
    width: 1200px; height: 652px;
    background: var(--paper);
  }
  .abs { position: absolute; }

  .brand {
    left: 213px; top: 18px;
    font-size: 26px; font-weight: 700; color: var(--teal);
    letter-spacing: 0.2px;
  }
  .main-nav {
    right: 212px; top: 23px;
    display: flex; gap: 15px;
    font-size: 11.6px; font-weight: 500;
  }
  .main-nav a {
    color: var(--teal-soft); text-decoration: none; position: relative;
  }
  .main-nav a.is-current { color: var(--teal); font-weight: 700; }
  .main-nav a.is-current::after {
    content: ""; position: absolute; left: 1px; right: 0; top: 20px;
    height: 2.5px; background: var(--teal);
  }

  .welcome-title {
    left: 213px; top: 152px;
    font-size: 25px; font-weight: 700; color: var(--teal);
    letter-spacing: -0.2px;
  }
  .welcome-sub {
    left: 213px; top: 186px;
    font-size: 16px; font-weight: 500; color: var(--teal);
  }
  .welcome-photo {
    left: 213px; top: 220px; width: 128px; height: 134px;
    background: linear-gradient(135deg, var(--photo-a) 0%, #d7e4ea 50%, var(--photo-b) 100%);
  }
  .welcome-text {
    left: 368px; top: 242px; width: 410px;
    font-size: 12px; line-height: 16.2px; color: var(--ink);
  }
  .rule {
    height: 2.5px; background: var(--teal);
  }
  .rule-services { left: 368px; top: 374px; width: 400px; }

  .service {
    width: 170px; text-align: center;
  }
  .service svg { display: block; margin: 0 auto; }
  .service-name {
    margin-top: 38px;
    font-size: 20px; font-weight: 500; color: var(--teal);
    line-height: 23px; letter-spacing: 0.3px;
  }

  .sidebar { left: 794px; width: 194px; }
  .sidebar .rule { width: 194px; }
  .sidebar h2 {
    margin-top: 2px;
    font-size: 11.6px; font-weight: 500; color: var(--teal);
  }
  .sidebar p {
    margin-top: 12px;
    font-size: 9.2px; line-height: 16.2px; color: var(--ink);
    white-space: nowrap;
  }
  .sidebar .more {
    display: block; text-align: right; margin-top: 11px; padding-right: 2px;
    font-size: 12px; font-weight: 500; color: var(--teal);
    text-decoration: underline; text-underline-offset: 2px;
  }
</style>
</head>
<body>
<div class="site">
  <header>
    <div class="abs brand">Dornaby</div>
    <nav class="abs main-nav">
      <a class="is-current" href="#">Home</a>
      <a href="#">About Us</a>
      <a href="#">Services</a>
      <a href="#">Experience</a>
      <a href="#">Resources</a>
      <a href="#">Contact Us</a>
    </nav>
  </header>

  <main>
    <h1 class="abs welcome-title">WELCOME TO OUR SITE</h1>
    <div class="abs welcome-sub">sample text</div>
    <div class="abs welcome-photo" role="img" aria-label="Photo of a businessman in a suit looking at a wall of financial charts"></div>
    <p class="abs welcome-text">Dornaby offers a flexible range of accounting and bookkeeping services and support for small and growing organizations in San Diego North County. We provide bookkeeping services specializing in LedgerLeaf® at your offices or remotely from ours. We also provide a broad range of accounting services or financial advice.</p>
    <div class="abs rule rule-services"></div>

    <div class="abs service" style="left:214px; top:403px;">
      <svg width="98" height="98" viewBox="0 0 98 98" aria-hidden="true">
        <circle cx="49" cy="49" r="47.5" fill="none" stroke="#33b8a4" stroke-width="2"/>
        <path d="M30 44 L58 36 L86 66 L40 80 Z" fill="#33b8a4"/>
        <path d="M38 52 L60 46 M41 58 L65 52 M44 64 L70 58 M47 70 L74 64" stroke="#fff" stroke-width="2.5"/>
        <ellipse cx="38" cy="17" rx="9" ry="4" fill="#33b8a4"/>
        <rect x="32" y="18" width="12" height="16" fill="#33b8a4"/>
        <ellipse cx="38" cy="35" rx="11" ry="4.5" fill="#33b8a4"/>
        <line x1="36" y1="38" x2="32" y2="50" stroke="#33b8a4" stroke-width="2"/>
      </svg>
      <div class="service-name">BOOKKEEPING</div>
    </div>

    <div class="abs service" style="left:401px; top:403px;">
      <svg width="98" height="98" viewBox="0 0 98 98" aria-hidden="true">
        <circle cx="49" cy="49" r="47.5" fill="none" stroke="#33b8a4" stroke-width="2"/>
        <path d="M38 30 V24 Q38 20 42 20 H56 Q60 20 60 24 V30" fill="none" stroke="#33b8a4" stroke-width="4"/>
        <rect x="24" y="30" width="50" height="40" rx="5" fill="#33b8a4"/>
        <rect x="24" y="47" width="50" height="2.5" fill="#fff"/>
        <circle cx="49" cy="48" r="3" fill="#fff"/>
      </svg>
      <div class="service-name">ACCOUNTING</div>
    </div>

    <div class="abs service" style="left:579px; top:403px;">
      <svg width="98" height="98" viewBox="0 0 98 98" aria-hidden="true">
        <circle cx="49" cy="49" r="47.5" fill="none" stroke="#33b8a4" stroke-width="2"/>
        <path d="M20 70 V54 L32 42 L44 54 L58 36 L70 26 V70 Z" fill="#33b8a4"/>
        <path d="M18 52 L32 38 L44 48 L72 20" fill="none" stroke="#33b8a4" stroke-width="5"/>
        <path d="M62 18 L76 14 L73 28 Z" fill="#33b8a4"/>
        <path d="M26 56 V70 M32 50 V70 M38 54 V70 M44 58 V70 M50 50 V70 M56 44 V70 M62 38 V70 M68 32 V70" stroke="#fff" stroke-width="2"/>
      </svg>
      <div class="service-name">BUSINESS<br>ADVICE</div>
    </div>
  </main>

  <aside>
    <section class="abs sidebar" style="top:163px;">
      <div class="rule"></div>
      <h2>About us</h2>
      <p>Lorem ipsum dolor sit amet, consectetur<br>adipiscing elit, sed do eiusmod tempor<br>incididunt ut labore et dolore magna<br>aliqua. Ut enim ad minim veniam, quis<br>nostrud exercitation ullamco laboris nisi ut<br>aliquip ex ea commodo consequat. Duis<br>aute irure dolor in reprehenderit in<br>voluptate velit esse cillum dolore eu fugiat</p>
      <a class="more" href="#">more info &gt;</a>
    </section>

    <section class="abs sidebar" style="top:374px;">
      <div class="rule"></div>
      <h2>Our strvices</h2>
      <p>Lorem ipsum dolor sit amet, consectetur<br>adipiscing elit, sed do eiusmod tempor<br>incididunt ut labore et dolore magna<br>aliqua. Ut enim ad minim veniam, quis<br>nostrud exercitation ullamco laboris nisi ut<br>aliquip ex ea commodo consequat. Duis<br>aute irure dolor in reprehenderit in<br>voluptate velit esse cillum dolore eu fugiat</p>
      <a class="more" href="#">more info &gt;</a>
    </section>
  </aside>
</div>
</body>
</html>
```